New Carpathian Table Billboard

Need to prepare a billboard for a KOSHER supermarket that is under new ownership. The billboard needs to have a good catch phrase such as:

A NEW Fresh KOSHER Grocery Experience Has Arrived!

The Legacy Continues...
Stop In To See The NEW Carpathian Table Foods!

Kosher Grocery Shopping at it's Finest!
Come See The NEW & IMPROVED Carpathian Table Foods

No Pictures. Choose various color backgrounds and send me proofs. Think of other catchy phrases and provide examples. Don't only use the phrases I gave above.

The store was taken under new ownership and we want to promote the NEW and Improved Store.

Target Market(s)

Orthodox Jewish

Industry/Entity Type

Grocery Store

Requirements
Must have
• Logo
• Linwell & Harbury in Skokie
Nice to have
• No Pictures.
Should not have
• Too much wording.

```html
<!DOCTYPE html>
<html lang="en">
<head>
<meta charset="utf-8">
<title>Carpathian Table Foods Billboard</title>
<link href="https://fonts.googleapis.com/css2?family=Archivo+Black&family=Russo+One&display=swap" rel="stylesheet">
<style>
  :root {
    --navy: #14213f;
    --red: #e8222b;
    --yellow: #ffe41a;
    --white: #ffffff;
    --page: #f2f2f2;
  }
  html, body {
    margin: 0;
    padding: 0;
    width: 1200px;
    height: 960px;
    overflow: hidden;
    background: var(--page);
  }
  .canvas {
    position: relative;
    width: 1200px;
    height: 960px;
  }
  .billboard {
    position: absolute;
    left: 20px;
    top: 430px;
    width: 1160px;
    height: 100px;
    display: block;
    box-shadow: 0 2px 10px rgba(0,0,0,0.15);
  }
  .headline { font-family: "Archivo Black", "Arial Black", sans-serif; }
  .brand-name { font-family: "Archivo Black", "Arial Black", sans-serif; fill: var(--navy); }
  .location { font-family: "Russo One", "Arial Black", sans-serif; }
  .ink-navy { fill: var(--navy); }
  .ink-red { fill: var(--red); }
  .ink-yellow { fill: var(--yellow); }
  .ink-white { fill: var(--white); }
</style>
</head>
<body>
<main class="canvas">
  <svg class="billboard" viewBox="0 0 1160 100" xmlns="http://www.w3.org/2000/svg" aria-label="Carpathian Table Foods billboard">
    <rect class="ink-white" x="0" y="0" width="1160" height="100"/>

    <g class="brand">
      <circle class="ink-red" cx="30" cy="50" r="20"/>
      <text class="brand-name" x="58" y="46" font-size="17" textLength="108" lengthAdjust="spacingAndGlyphs">Carpathian</text>
      <text class="brand-name" x="58" y="67" font-size="17">Table</text>
    </g>

    <g class="headline">
      <text x="511" y="54" font-size="44" text-anchor="middle" textLength="600" lengthAdjust="spacingAndGlyphs"><tspan class="ink-navy">A </tspan><tspan class="ink-red">NEW </tspan><tspan class="ink-navy">Fresh </tspan><tspan class="ink-red">KOSHER</tspan></text>
      <text class="ink-navy" x="511" y="89" font-size="29" text-anchor="middle" textLength="676" lengthAdjust="spacingAndGlyphs">Grocery Experience Has Arrived!</text>
    </g>

    <g class="accent-stripes">
      <path class="ink-navy" d="M872 100 C 905 72, 925 35, 938 0 L 952 0 C 938 35, 918 72, 888 100 Z"/>
      <path class="ink-red" d="M896 100 C 930 70, 952 35, 966 0 L 980 0 C 966 35, 944 70, 910 100 Z"/>
      <path class="ink-navy" d="M918 100 C 952 70, 975 35, 990 0 L 1160 0 L 1160 100 Z"/>
    </g>

    <g class="location" text-anchor="middle">
      <text class="ink-red" x="1068" y="33" font-size="23">Linwell</text>
      <text x="1068" y="60" font-size="23"><tspan class="ink-yellow">&amp; </tspan><tspan class="ink-red">Harbury</tspan></text>
      <text class="ink-yellow" x="1068" y="87" font-size="23">in Skokie</text>
    </g>
  </svg>
</main>
</body>
</html>
```